Business Card Design for a Personal Trainer

I need a business card design for my job as a personal trainer. It should have a unique, modern and exclusive design. On the front there should be only my logo with my name and my job. 0162/3819204 Tobias Lendhart Wiesengrundweg 14 80417 Munich Germany The most important contact information is the web adress. it can be bigger than the rest, but its not necessary. The card should be 8,5cmx5,5cm big. Font: Roboto. Colors: black, white, gray, 56c1ff.

```html
<!DOCTYPE html>
<html lang="de">
<head>
<meta charset="utf-8">
<title>Tobias Lendhart – Visitenkarte</title>
<link href="https://fonts.googleapis.com/css2?family=Open+Sans:wght@400;600&display=swap" rel="stylesheet">
<style>
  :root {
    --stage: #e4e4e4;
    --card-black: #050505;
    --swoosh-gray: #6e6e6e;
    --photo-dark: #1c1c1c;
    --photo-mid: #4a4a4a;
    --text-white: #ffffff;
    --text-soft: #e8e8e8;
    --rule: #cfcfcf;
  }
  * { box-sizing: border-box; margin: 0; padding: 0; }
  html, body {
    width: 1200px; height: 864px; overflow: hidden;
    background: var(--stage);
    font-family: "Open Sans", Arial, sans-serif;
  }
  .stage {
    position: relative; width: 1200px; height: 864px;
    display: flex; align-items: center; justify-content: center; gap: 40px;
  }
  .card {
    position: relative; width: 540px; height: 350px;
    background: var(--card-black); overflow: hidden;
    color: var(--text-white);
  }

  /* Wordmark block: name + job title */
  .brand-block { display: inline-flex; flex-direction: column; align-items: stretch; }
  .brand-name {
    font-weight: 400; font-size: 21px; letter-spacing: 1px; line-height: 1.1;
    text-transform: uppercase; color: var(--text-white);
    display: flex; align-items: center; justify-content: center; gap: 9px;
    white-space: nowrap;
  }
  .brand-mark { width: 13px; height: 13px; background: var(--text-white); flex: none; }
  .brand-title {
    margin-top: 4px;
    display: flex; align-items: center; gap: 8px;
    font-size: 9px; letter-spacing: 3px; text-transform: uppercase;
    color: var(--text-white); white-space: nowrap;
  }
  .brand-title::before, .brand-title::after {
    content: ""; flex: 1; height: 1px; background: var(--rule);
  }

  /* Contact side */
  .contact-photo {
    position: absolute; left: 0; top: 0; width: 260px; height: 350px;
    background: radial-gradient(ellipse at 45% 45%, var(--photo-mid) 0%, var(--photo-dark) 55%, var(--card-black) 90%);
  }
  .contact-swoosh { position: absolute; left: 0; top: 0; width: 540px; height: 350px; }
  .contact-info {
    position: absolute; left: 300px; right: 14px; top: 66px;
    text-align: center;
  }
  .holder-name { margin-top: 26px; font-weight: 600; font-size: 18px; }
  .contact-lines { margin-top: 22px; font-size: 14px; line-height: 1.45; color: var(--text-soft); }
  .contact-lines .gap { margin-top: 14px; }

  /* Brand side */
  .brand-side .collage {
    position: absolute; left: 34px; top: 30px; right: 34px; bottom: 30px;
    background: linear-gradient(120deg, #2a2a2a 0%, #5a5a5a 40%, #3a3a3a 65%, #1a1a1a 100%);
  }
  .brand-side .overlay {
    position: absolute; left: 34px; right: 34px; top: 30px; bottom: 30px;
    display: flex; flex-direction: column; align-items: center; justify-content: center;
  }
  .brand-side .brand-name { font-size: 27px; }
  .brand-side .brand-title { font-size: 11px; letter-spacing: 4px; }
  .web-address { margin-top: 34px; font-size: 25px; letter-spacing: 0.5px; white-space: nowrap; }
</style>
</head>
<body>
<main class="stage">

  <section class="card brand-side">
    <div class="collage" role="img" aria-label="Schwarz-weiße Fotocollage mit Trainingsszenen im Fitnessstudio"></div>
    <div class="overlay">
      <div class="brand-block">
        <div class="brand-name"><span class="brand-mark"></span>Tobias Lendhart</div>
        <div class="brand-title">Personal Trainer</div>
      </div>
      <div class="web-address">www.tobiaslendhart.de</div>
    </div>
  </section>

  <section class="card contact-side">
    <div class="contact-photo" role="img" aria-label="Schwarz-weißes Porträt des Trainers mit verschränkten Armen"></div>
    <svg class="contact-swoosh" viewBox="0 0 540 350" aria-hidden="true">
      <path d="M250 0 C 300 110, 290 250, 150 350 L 175 350 C 305 250, 320 110, 268 0 Z" fill="var(--swoosh-gray)"/>
      <path d="M268 0 C 320 110, 305 250, 175 350 L 540 350 L 540 0 Z" fill="var(--card-black)"/>
    </svg>
    <div class="contact-info">
      <div class="brand-block">
        <div class="brand-name"><span class="brand-mark"></span>Tobias Lendhart</div>
        <div class="brand-title">Personal Trainer</div>
      </div>
      <div class="holder-name">Tobias Lendhart</div>
      <div class="contact-lines">
        <div>0162/3819204</div>
        <div class="gap">t.lendhart@mailpost.de</div>
        <div>Wiesengrundweg 14</div>
        <div>80417 München</div>
      </div>
    </div>
  </section>

</main>
</body>
</html>
```